Modern business card design for professional copywriter

I'd like a business card design that I can use to have my cards printed out by quillprint.com as a squared corners business card (see artwork and design guidelines here: https://help.quillprint.com/hc/en-gb/sections/200570950-QUILL-Product-Templates)

The design should be clean and modern and reflect the colours, tone and branding on my website: https://tessavorrin.com.au

Target Market(s)

Professionals, B2B small business owners

Industry/Entity Type

Business

Contact Information for Business Card

Tessa Vorrin
m: 0468 905 327
e: tessa@tessavorrin.com.au
w: tessavorrin.com.au

Font styles to use
Sans Serif

Requirements
Must have
• Tagline: "Smart copywriting for clever business people"
• Brand colours: fd8000, 009984, 666666 and black
Nice to have

```html
<!DOCTYPE html>
<html lang="en">
<head>
<meta charset="utf-8">
<title>Tessa Vorrin – Business Card</title>
<link rel="stylesheet" href="https://fonts.googleapis.com/css2?family=Lato:ital,wght@0,400;0,700;1,400&family=Tinos:ital,wght@1,700&display=swap">
<style>
  :root {
    --teal: #009984;
    --teal-light: #37a592;
    --teal-dark: #2b8b77;
    --orange: #fd8000;
    --grey: #666666;
    --black: #000000;
    --white: #ffffff;
    --page: #eeeeee;
  }
  * { margin: 0; padding: 0; box-sizing: border-box; }
  html, body { width: 1200px; height: 586px; overflow: hidden; }
  body {
    background: var(--page);
    font-family: "Lato", sans-serif;
    position: relative;
  }
  .card {
    position: absolute;
    top: 129px;
    width: 502px;
    height: 301px;
    overflow: hidden;
  }
  .card--front { left: 61px; }
  .card--back { left: 619px; background: var(--white); }

  .front-texture {
    position: absolute; inset: 0;
    background: linear-gradient(135deg, var(--teal-light) 0%, var(--teal-dark) 50%, var(--teal-light) 100%);
  }
  .brand-name {
    position: absolute;
    left: 0; right: 0;
    text-align: center;
    font-family: "Lato", sans-serif;
    font-weight: 400;
    letter-spacing: -0.5px;
  }
  .card--front .brand-name {
    top: 106px;
    font-size: 50px;
    color: var(--white);
  }
  .card--back .brand-name {
    top: 44px;
    font-size: 36px;
    color: var(--teal);
  }
  .tagline {
    position: absolute;
    top: 248px; left: 0; right: 0;
    text-align: center;
    font-family: "Tinos", serif;
    font-style: italic;
    font-weight: 700;
    font-size: 12.5px;
    color: #1d3c35;
  }

  .contact {
    position: absolute;
    left: 28px; top: 207px;
    list-style: none;
  }
  .contact li {
    display: flex; align-items: center;
    height: 24px;
    font-size: 12.5px;
    color: var(--black);
  }
  .contact-icon {
    width: 17px; height: 17px;
    margin-right: 8px;
    flex: none;
  }
  .contact .web {
    color: var(--teal);
    font-weight: 700;
    font-size: 12.5px;
  }

  .social {
    position: absolute;
    right: 23px; top: 190px;
    display: flex; gap: 3px;
  }
  .social span {
    width: 22px; height: 22px;
    border-radius: 50%;
    background: var(--orange);
  }

  .services {
    position: absolute;
    right: 24px; top: 219px;
    text-align: right;
    list-style: none;
  }
  .services li {
    height: 18.5px;
    font-size: 11.2px;
    font-weight: 700;
    color: var(--black);
    letter-spacing: -0.2px;
  }
  .services .dot { color: var(--teal); }

  .band-teal {
    position: absolute; left: 0; right: 0;
    top: 285px; height: 5px;
    background: var(--teal);
  }
  .band-orange {
    position: absolute; left: 0; right: 0;
    top: 290px; height: 11px;
    background: var(--orange);
  }
</style>
</head>
<body>

<section class="card card--front">
  <div class="front-texture" role="img" aria-label="Faceted teal low-poly geometric background"></div>
  <div class="brand-name">Tessa Vorrin</div>
  <p class="tagline">Smart copywriting for clever business people</p>
</section>

<section class="card card--back">
  <div class="brand-name">Tessa Vorrin</div>

  <ul class="contact">
    <li>
      <svg class="contact-icon" viewBox="0 0 18 18" aria-hidden="true">
        <circle cx="9" cy="9" r="9" fill="#009984"/>
        <path d="M4.5 7.5c0-1.2 2-2 4.5-2s4.5.8 4.5 2v.8h-2.2V7.2H6.7v1.1H4.5z M6 9h6l1 3.5H5z" fill="#fff"/>
      </svg>
      0468 905 327
    </li>
    <li>
      <svg class="contact-icon" viewBox="0 0 18 18" aria-hidden="true">
        <circle cx="9" cy="9" r="9" fill="#009984"/>
        <rect x="4.5" y="5.8" width="9" height="6.4" fill="none" stroke="#fff" stroke-width="1.2"/>
        <path d="M4.5 5.8 9 9.6l4.5-3.8" fill="none" stroke="#fff" stroke-width="1.2"/>
      </svg>
      tessa@tessavorrin.com.au
    </li>
    <li class="web">www.tessavorrin.com.au</li>
  </ul>

  <div class="social" aria-label="Social profiles">
    <span></span><span></span><span></span><span></span>
  </div>

  <ul class="services">
    <li>SEO Copywriting <span class="dot">•</span> Feature Writing</li>
    <li>Content Marketing <span class="dot">•</span> Legal Copywriting</li>
    <li>Small Business Copywriting <span class="dot">•</span> Website Copywriting</li>
  </ul>

  <div class="band-teal"></div>
  <div class="band-orange"></div>
</section>

</body>
</html>
```